Business card design for my company.
I would like the card's background colour to be black. You can also see our web site to get an idea of our brand. https://www.tmwhomecrafting.com.au/
- Name
- Email

```html
<!DOCTYPE html>
<html lang="en">
<head>
<meta charset="utf-8">
<title>TMW Home Crafting – Business Card</title>
<link rel="stylesheet" href="https://fonts.googleapis.com/css2?family=Montserrat:wght@400;500;700&display=swap">
<style>
  :root {
    --stage: #2b2b2b;
    --card: #151515;
    --white: #f2f2f2;
    --green: #11974a;
  }
  * { margin: 0; padding: 0; box-sizing: border-box; }
  html, body {
    width: 1200px;
    height: 689px;
    overflow: hidden;
    background: var(--stage);
    font-family: "Montserrat", sans-serif;
  }
  .stage {
    position: relative;
    width: 1200px;
    height: 689px;
    display: flex;
    align-items: center;
    justify-content: center;
    gap: 60px;
  }
  .card {
    width: 510px;
    height: 310px;
    background: var(--card);
    border-radius: 18px;
    box-shadow: 0 18px 40px rgba(0,0,0,0.45);
    position: relative;
    overflow: hidden;
  }
  /* Front */
  .card--front {
    display: flex;
    align-items: center;
    justify-content: center;
    gap: 16px;
  }
  .brand-mark {
    width: 26px;
    height: 26px;
    background: var(--white);
  }
  .brand-name {
    color: var(--white);
    font-weight: 700;
    font-size: 30px;
    letter-spacing: 3px;
    text-transform: uppercase;
  }
  /* Back */
  .card--back {
    display: flex;
    align-items: center;
    justify-content: center;
    padding: 0 24px;
  }
  .identity {
    text-align: right;
    flex: 0 0 auto;
  }
  .identity__name {
    color: var(--green);
    font-weight: 700;
    font-size: 26px;
    line-height: 1.05;
    white-space: nowrap;
  }
  .identity__role {
    color: var(--white);
    font-weight: 400;
    font-size: 13.5px;
    letter-spacing: 0.5px;
    margin-top: 4px;
    white-space: nowrap;
  }
  .divider {
    width: 1.5px;
    height: 84px;
    background: var(--green);
    margin: 0 14px;
    flex: 0 0 auto;
  }
  .contact {
    list-style: none;
    display: flex;
    flex-direction: column;
    gap: 8px;
    flex: 0 0 auto;
  }
  .contact__item {
    display: flex;
    align-items: center;
    gap: 7px;
    color: var(--white);
    font-size: 12px;
    font-weight: 400;
    white-space: nowrap;
  }
  .contact__icon {
    width: 12px;
    height: 12px;
    flex: 0 0 auto;
    fill: var(--green);
  }
</style>
</head>
<body>
<main class="stage">
  <section class="card card--front" aria-label="Card front">
    <span class="brand-mark" aria-hidden="true"></span>
    <span class="brand-name">TMW Home Crafting</span>
  </section>

  <section class="card card--back" aria-label="Card back">
    <div class="identity">
      <p class="identity__name">Liam Harcourt</p>
      <p class="identity__role">General Manager</p>
    </div>
    <span class="divider" aria-hidden="true"></span>
    <ul class="contact">
      <li class="contact__item">
        <svg class="contact__icon" viewBox="0 0 16 16" aria-hidden="true">
          <path d="M2 5c0-2 3-3 6-3s6 1 6 3v1.5h-3.5V5H5.5v1.5H2z M4 8h8l1.5 6h-11z"/>
        </svg>
        0400 123 456
      </li>
      <li class="contact__item">
        <svg class="contact__icon" viewBox="0 0 16 16" aria-hidden="true">
          <path d="M1 3h14v10H1z M2 4l6 5 6-5" stroke="#151515" stroke-width="1.2"/>
        </svg>
        info@tmwhomecrafting.com.au
      </li>
      <li class="contact__item">
        <svg class="contact__icon" viewBox="0 0 16 16" aria-hidden="true">
          <circle cx="8" cy="8" r="7"/>
          <path d="M1 8h14 M8 1c-3 3-3 11 0 14 M8 1c3 3 3 11 0 14" stroke="#151515" stroke-width="1" fill="none"/>
        </svg>
        www.tmwhomecrafting.com.au
      </li>
    </ul>
  </section>
</main>
</body>
</html>
```